Colin Vardek Business card

Hey there, I’m hoping to have a business card designed. I’m in Real estate and just switched to a new Brokerage called: The Harbourline Property Group

The back could just be the company name maybe or whatever looks good!

I’ve attached some logos of our company and some cards my buddy had done up.

On the card:
Colin Vardek
colinvardek@mailora.com
587-412-9065
colinvardek.ca

Target Market(s)

Home buyers and sellers

Industry/Entity Type

Real Estate

Contact Information for Business Card

just looking for a cool and modern design with my picture on it. I like the idea of Black and red being used.

Requirements
Must have
• all the details provided. I'm open to anything. Just want a professional looking card.

```html
<!DOCTYPE html>
<html lang="en">
<head>
<meta charset="utf-8">
<title>Colin Vardek Business Card</title>
<link rel="stylesheet" href="https://fonts.googleapis.com/css2?family=Poppins:wght@300;400;600;700&display=swap">
<style>
  :root {
    --stage: #1e1e20;
    --card: #222226;
    --red: #d0223a;
    --white: #ffffff;
    --photo-light: #f3f3f3;
    --photo-dark: #3a3f48;
  }
  * { margin: 0; padding: 0; box-sizing: border-box; }
  html, body {
    width: 1200px; height: 711px; overflow: hidden;
    background: var(--stage);
    font-family: "Poppins", sans-serif;
  }
  .stage {
    width: 1200px; height: 711px;
    display: flex; align-items: center; justify-content: center; gap: 30px;
  }
  .card {
    position: relative;
    width: 560px; height: 320px;
    background: var(--card);
    border-radius: 22px;
    box-shadow: 0 5px 0 var(--red);
    overflow: hidden;
  }
  /* Back */
  .card-back { display: flex; align-items: center; justify-content: center; }
  .brand-back {
    display: flex; align-items: center; gap: 14px;
    color: var(--white); font-weight: 700; font-size: 30px; line-height: 1.1;
    text-transform: uppercase; letter-spacing: 0.5px;
  }
  .brand-back .mark { width: 22px; height: 22px; background: var(--red); flex: none; }
  /* Front */
  .portrait-art { position: absolute; inset: 0; }
  .brand-front {
    position: absolute; left: 26px; top: 26px;
    display: flex; align-items: center; gap: 10px;
    color: var(--white); font-weight: 700; font-size: 15px; line-height: 1.15;
    text-transform: uppercase; width: 230px;
  }
  .brand-front .mark { width: 12px; height: 12px; background: var(--red); flex: none; }
  .name-bar {
    position: absolute; left: 0; top: 158px; width: 8px; height: 40px; background: var(--red);
  }
  .agent-name {
    position: absolute; left: 26px; top: 156px;
    font-size: 32px; color: var(--white); font-weight: 300;
  }
  .agent-name .first { color: var(--red); font-weight: 700; }
  .contact-list {
    position: absolute; left: 26px; top: 238px; list-style: none;
    font-size: 12.5px; color: var(--white); font-weight: 300; line-height: 22px;
  }
  .contact-list li { display: flex; align-items: center; gap: 9px; }
  .contact-list svg { width: 13px; height: 13px; fill: var(--red); flex: none; }
</style>
</head>
<body>
<main class="stage">
  <section class="card card-back">
    <div class="brand-back"><span class="mark"></span><span>The Harbourline<br>Property Group</span></div>
  </section>

  <section class="card card-front">
    <svg class="portrait-art" viewBox="0 0 560 320" width="560" height="320">
      <defs>
        <linearGradient id="portraitTone" x1="0" y1="0" x2="0" y2="1">
          <stop offset="0" stop-color="var(--photo-light)"/>
          <stop offset="0.55" stop-color="#e6e4e2"/>
          <stop offset="1" stop-color="var(--photo-dark)"/>
        </linearGradient>
      </defs>
      <circle cx="465" cy="70" r="265" fill="var(--red)"/>
      <circle cx="490" cy="55" r="255" fill="url(#portraitTone)" role="img" aria-label="Portrait photo of Colin Vardek in a dark suit and white shirt"/>
    </svg>

    <div class="brand-front"><span class="mark"></span><span>The Harbourline Property Group</span></div>

    <span class="name-bar"></span>
    <h1 class="agent-name"><span class="first">Colin</span> Vardek</h1>

    <ul class="contact-list">
      <li><svg viewBox="0 0 24 24"><path d="M6.6 10.8a15.1 15.1 0 0 0 6.6 6.6l2.2-2.2a1 1 0 0 1 1-.25 11.4 11.4 0 0 0 3.6.57 1 1 0 0 1 1 1V20a1 1 0 0 1-1 1A17 17 0 0 1 3 4a1 1 0 0 1 1-1h3.5a1 1 0 0 1 1 1c0 1.25.2 2.45.57 3.6a1 1 0 0 1-.25 1z"/></svg>587-412-9065</li>
      <li><svg viewBox="0 0 24 24"><path d="M12 2a10 10 0 1 0 0 20 10 10 0 0 0 0-20zm6.9 6h-2.9a15.6 15.6 0 0 0-1.4-3.6A8 8 0 0 1 18.9 8zM12 4c.8 1.2 1.5 2.5 1.9 4h-3.8c.4-1.5 1.1-2.8 1.9-4zM4.3 14a8.2 8.2 0 0 1 0-4h3.4a16.5 16.5 0 0 0 0 4zm.8 2h2.9c.3 1.3.8 2.5 1.4 3.6A8 8 0 0 1 5.1 16zM8 8H5.1a8 8 0 0 1 4.3-3.6C8.8 5.5 8.3 6.7 8 8zm4 12c-.8-1.2-1.5-2.5-1.9-4h3.8c-.4 1.5-1.1 2.8-1.9 4zm2.3-6H9.7a14.7 14.7 0 0 1 0-4h4.6a14.7 14.7 0 0 1 0 4zm.3 5.6c.6-1.1 1.1-2.3 1.4-3.6h2.9a8 8 0 0 1-4.3 3.6zm1.7-5.6a16.5 16.5 0 0 0 0-4h3.4a8.2 8.2 0 0 1 0 4z"/></svg>www.colinvardek.ca</li>
      <li><svg viewBox="0 0 24 24"><path d="M20 4H4a2 2 0 0 0-2 2v12a2 2 0 0 0 2 2h16a2 2 0 0 0 2-2V6a2 2 0 0 0-2-2zm0 4-8 5-8-5V6l8 5 8-5z"/></svg>colinvardek@mailora.com</li>
    </ul>
  </section>
</main>
</body>
</html>
```